Build a landing page to promote a service (dialler consultation and support).

We are a call centre consultation firm and we need a landing page to promote a service. The service is Tormalux dialler consultation and support.
If you do not know what Tormalux is, please do some quick "Zorvex" research for more information.
The landing page will be promoted with a paid advertisement, so we want something that is simple, and explains exactly what service we offer.
There are two objectives for the landing page:
1) A "call to action" which directs the user to a contact page, including a form plus all of our contact details.
2) A form for them viewers to enter their details to get a "FREE" quote for their project. This form should be placed on the main page.
Notes:
The call to action will require the viewer to enter their name, email, phone number as well as a description of their request. There will also need to be a drop down menu for the type of quote. This menu should have the following options:
1) Tormalux support
2) Tormalux hosting
3) Tormalux customisation
4) Other
We need 2 pages in total:
1) Main landing page
This is the home page. It will need to clearly indicate our services and our key selling features.
Services:
* Tormalux support
* Tormalux hosting
* Tormalux customisation
Key Selling Features:
* Australian based
* PCI complaint
* 10+ years of dialler and call centre experience
* we run a sister company which is a highly reputable 40 seat call centre, so we know first hand about call centre technology.
The main landing page will have an "about us" section with a few paragraphs about how we got started.
-------------------------------------------------------------------------
2) Contact page
All of our contact details will live on this page, as well as a contact form.
Other notes:
We will be self hosting the landing page.
We already have a domain name.
The design must be clean and incorporate our logo, as well as it's colours. (Logo attached)
We want a fully function HTML landing page, not just a "PSD" design.
The page must be mobile optimised.
Anyone using Tormalux software.

```html
<!DOCTYPE html>
<html lang="en">
<head>
<meta charset="utf-8">
<title>BrightLine – Tormalux Dialler Support</title>
<link href="https://fonts.googleapis.com/css2?family=Montserrat:wght@400;500;600;700&display=swap" rel="stylesheet">
<style>
:root{
  --teal:#1ba58f;
  --blue:#1a7fca;
  --ink:#4a4a4a;
  --muted:#5c5c5c;
  --page:#eeeeee;
  --white:#ffffff;
  --line:#d6d6d6;
  --panel:rgba(60,60,60,.82);
  --grey-mark:#b3b3b3;
}
*{box-sizing:border-box;margin:0;padding:0}
html,body{width:1200px;height:2329px;overflow:hidden}
body{position:relative;background:var(--page);font-family:"Montserrat",Arial,sans-serif;color:var(--ink)}
.abs{position:absolute}

/* header */
.site-header{left:0;top:0;width:1200px;height:123px;background:var(--white)}
.brand{left:160px;top:14px;width:154px;display:flex;flex-direction:column;align-items:center;gap:4px}
.brand-dot{width:62px;height:62px;border-radius:50%;background:var(--blue);flex:none}
.brand-name{font-weight:600;font-size:27px;line-height:32px;color:var(--blue);letter-spacing:.5px;white-space:nowrap}
.header-phone{right:162px;top:18px;font-weight:600;font-size:17px;color:var(--blue);display:flex;align-items:center;gap:5px}
.main-nav{right:162px;top:66px;display:flex;align-items:center;gap:36px;font-weight:600;font-size:16px;color:var(--ink)}
.nav-cta{background:var(--teal);color:var(--white);padding:8px 12px;font-size:16px}

/* hero */
.hero{left:0;top:123px;width:1200px;height:585px;background:linear-gradient(100deg,#4e4a48 0%,#8a6e63 30%,#b07c66 52%,#6b6662 75%,#3e4345 100%)}
.hero-title{left:162px;top:468px;color:var(--white);font-weight:700;line-height:1}
.hero-title .small{display:block;font-size:48px}
.hero-title .big{display:block;font-size:66px;margin-top:8px}
.quote-panel{left:727px;top:229px;width:311px;height:372px;background:var(--panel);padding:16px 30px 0}
.quote-panel h2{color:var(--white);font-size:31px;font-weight:600;text-align:center;margin-bottom:8px}
.field{color:var(--white);font-size:12px;border-bottom:2px solid #e8e8e8;height:36px;padding-top:2px;display:flex;justify-content:space-between}
.field.tall{height:78px;padding-top:10px}
.field.select{padding-top:12px}
.quote-btn{margin-top:14px;height:40px;background:linear-gradient(90deg,var(--teal),var(--blue));color:var(--white);font-weight:600;font-size:19px;display:flex;align-items:center;justify-content:center}
.slider-dots{left:574px;top:640px;display:flex;gap:4px}
.slider-dots span{width:13px;height:13px;border-radius:50%;background:var(--white)}
.slider-dots span.on{border:3px solid var(--white);background:var(--blue)}

/* services */
.section-title{width:1200px;left:0;text-align:center;font-weight:600;color:var(--ink);letter-spacing:2px}
.services-title{top:744px;font-size:38px}
.services-intro{left:370px;top:806px;width:460px;text-align:center;font-size:14.5px;line-height:23px;color:var(--muted)}
.service-card{top:930px;width:280px;height:258px;background:#f7f7f7;box-shadow:0 1px 5px rgba(0,0,0,.15);text-align:center;padding-top:98px}
.service-card h3{font-size:19px;font-weight:600;color:var(--ink);margin-bottom:14px;white-space:nowrap}
.service-card p{font-size:12.5px;line-height:23px;color:var(--muted);padding:0 18px}
.service-icon{top:875px;width:132px;height:132px;border-radius:50%;border:5px solid var(--teal);background:var(--white);padding:5px}
.service-icon div{width:100%;height:100%;border-radius:50%;background:var(--blue);display:flex;align-items:center;justify-content:center}

/* features */
.features{left:162px;top:1236px;width:876px;height:308px;background:linear-gradient(90deg,#1ca892 0%,#1d9aa6 45%,#1b80c8 100%)}
.features h2{left:41px;top:40px;color:var(--white);font-size:37px;font-weight:600;letter-spacing:3px;line-height:40px}
.features ul{left:44px;top:134px;width:500px;list-style:none;color:var(--white);font-size:13.5px}
.features li{margin-bottom:11px;line-height:17px;padding-left:12px;position:relative}
.features li::before{content:"";position:absolute;left:0;top:6px;width:5px;height:5px;border-radius:50%;background:var(--white)}
.features-photo{left:560px;top:24px;width:268px;height:268px;border-radius:50%;border:8px solid #163a66;background:radial-gradient(circle at 45% 45%,#c9714c 0%,#8a4a34 40%,#2a2f3a 75%)}

/* about */
.about-photo{left:146px;top:1602px;width:540px;height:386px;background:linear-gradient(120deg,#d6e2ea 0%,#bfcfd9 35%,#e6dccf 60%,#9fb3c2 100%)}
.about-card{left:686px;top:1602px;width:352px;height:386px;background:var(--white);padding:40px 48px 0}
.about-card h2{font-size:38px;font-weight:600;letter-spacing:2px;color:var(--ink);margin-bottom:14px}
.about-card p{font-size:14px;line-height:22.5px;color:var(--muted)}
.about-btn{display:inline-block;margin-top:20px;background:linear-gradient(90deg,var(--teal),#1b8fb2);color:var(--white);font-size:14px;font-weight:500;padding:11px 14px}

/* footer */
.site-footer{left:0;top:2068px;width:1200px;height:261px;background:var(--white);border-top:4px solid;border-image:linear-gradient(90deg,var(--teal),var(--blue)) 1}
.footer-brand{left:160px;top:40px;width:200px;display:flex;flex-direction:column;align-items:center;gap:8px}
.footer-brand .brand-dot{background:var(--grey-mark);width:88px;height:88px}
.footer-brand .brand-name{color:#a9a9a9;font-size:30px;line-height:36px}
.footer-col{top:44px}
.footer-col h4{font-size:15px;font-weight:600;color:var(--blue);margin-bottom:14px}
.footer-col li{list-style:none;font-size:12.5px;color:var(--ink);line-height:25.5px;white-space:nowrap}
.social{display:flex;gap:16px;align-items:center;margin-top:4px}
.social .dot{width:20px;height:20px;border-radius:50%;background:#1e1e1e}
.footer-rule{left:162px;top:214px;width:876px;height:1px;background:#e3e3e3}
.copyright{left:0;top:228px;width:1200px;text-align:center;font-size:12.5px;color:var(--ink)}
</style>
</head>
<body>

<header class="site-header abs">
  <div class="brand abs"><span class="brand-dot"></span><span class="brand-name">BrightLine</span></div>
  <div class="header-phone abs">
    <svg width="14" height="14" viewBox="0 0 24 24"><path fill="#1a7fca" d="M6.6 10.8a15 15 0 0 0 6.6 6.6l2.2-2.2c.3-.3.7-.4 1-.2 1.1.4 2.3.6 3.6.6.6 0 1 .4 1 1V20c0 .6-.4 1-1 1A17 17 0 0 1 3 4c0-.6.4-1 1-1h3.5c.6 0 1 .4 1 1 0 1.3.2 2.5.6 3.6.1.3 0 .7-.2 1z"/></svg>
    Phone: 555-013-2740
  </div>
  <nav class="main-nav abs">
    <span>Home</span><span>About Us</span><span>Services</span><span>News</span><span class="nav-cta">Contact Us</span>
  </nav>
</header>

<section class="hero abs" role="img" aria-label="Photo of smiling call centre agents wearing headsets"></section>
<h1 class="hero-title abs"><span class="small">Welcome to</span><span class="big">Brightline</span></h1>

<form class="quote-panel abs">
  <h2>Get a Quote</h2>
  <div class="field">Name</div>
  <div class="field">Email</div>
  <div class="field">Phone number</div>
  <div class="field select"><span>Tormalux support</span><svg width="10" height="8" viewBox="0 0 10 8"><path d="M0 0h10L5 7z" fill="#fff"/></svg></div>
  <div class="field tall">Description</div>
  <div class="quote-btn">Get a Free Quote</div>
</form>

<div class="slider-dots abs"><span></span><span class="on"></span><span></span></div>

<h2 class="section-title services-title abs">Services</h2>
<p class="services-intro abs">Lorem ipsum dolor sit amet, consectetur adipiscing elit, sed do eiusmor incididunt ut labore et dolore magna aliqua.</p>

<article class="service-card abs" style="left:162px">
  <h3>Tormalux Support</h3>
  <p>Lorem ipsum dolor sit ametco nsectetur adipiscing elit, sed do eiusmor incididunt ut labore et dolore magna aliqua.</p>
</article>
<article class="service-card abs" style="left:459px">
  <h3>Tormalux Hosting</h3>
  <p>Lorem ipsum dolor sit ametco nsectetur adipiscing elit, sed do eiusmor incididunt ut labore et dolore magna aliqua.</p>
</article>
<article class="service-card abs" style="left:755px">
  <h3>Tormalux Customisation</h3>
  <p>Lorem ipsum dolor sit ametco nsectetur adipiscing elit, sed do eiusmor incididunt ut labore et dolore magna aliqua.</p>
</article>

<div class="service-icon abs" style="left:236px"><div>
  <svg width="64" height="64" viewBox="0 0 64 64" fill="none" stroke="#fff" stroke-width="2.5"><path d="M16 30a16 16 0 0 1 32 0"/><rect x="12" y="28" width="8" height="12" rx="3"/><rect x="44" y="28" width="8" height="12" rx="3"/><circle cx="32" cy="32" r="9"/><path d="M16 58c2-9 8-13 16-13s14 4 16 13"/><path d="M48 40c0 4-4 6-10 6"/></svg>
</div></div>
<div class="service-icon abs" style="left:533px"><div>
  <svg width="66" height="64" viewBox="0 0 66 64" fill="none" stroke="#fff" stroke-width="2.5"><path d="M18 38a10 10 0 0 1 0-20 14 14 0 0 1 27-3 11 11 0 0 1 3 23z"/><path d="M24 38v10M33 38v16M42 38v10"/><circle cx="24" cy="51" r="3"/><circle cx="33" cy="57" r="3"/><circle cx="42" cy="51" r="3"/></svg>
</div></div>
<div class="service-icon abs" style="left:830px"><div>
  <svg width="66" height="66" viewBox="0 0 66 66" fill="none" stroke="#fff" stroke-width="2.5"><circle cx="33" cy="33" r="22"/><path d="M33 5v5M33 56v5M5 33h5M56 33h5M13 13l4 4M49 49l4 4M53 13l-4 4M13 53l4-4"/><path d="M23 26c2-3 5-3 6 0l1 3-2 2c1 3 3 5 6 6l2-2 3 1c3 1 3 4 0 6-7 3-19-9-16-16z"/><text x="36" y="28" font-size="11" font-family="Montserrat,sans-serif" fill="#fff" stroke="none" font-weight="700">24</text></svg>
</div></div>

<section class="features abs">
  <h2 class="abs">Key Selling<br>Features</h2>
  <ul class="abs">
    <li>Australian based</li>
    <li>PCI complaint</li>
    <li>10+ years of dialler and call centre experience</li>
    <li>We run a sister company which is a highly reputable 40 seat call centre, so we know first hand about call centre technology.</li>
  </ul>
  <div class="features-photo abs" role="img" aria-label="Photo of a smiling agent with a headset framed in a circle"></div>
</section>

<div class="about-photo abs" role="img" aria-label="Photo of two agents with headsets working at computers"></div>
<section class="about-card abs">
  <h2>About Us</h2>
  <p>Lorem ipsum dolor sit amet, conse ctetur adipiscing elit, sed doeiusmo rincididunt ut labore et dolore mag na alirem ipsum dolor sit amet, cose ctetur adipiscing elit, sed doeiusmo rincididunt ut labore et dolore mag na aliquLorem ipsum dolor sit amet, ctetur adipiscing.</p>
  <span class="about-btn">Get Started</span>
</section>

<footer class="site-footer abs">
  <div class="footer-brand abs"><span class="brand-dot"></span><span class="brand-name">BrightLine</span></div>
  <div class="footer-col abs" style="left:406px"><h4>Services</h4><ul><li>Tormalux support</li><li>Tormalux hosting</li><li>Tormalux customisation</li><li>Other</li></ul></div>
  <div class="footer-col abs" style="left:601px"><h4>Links</h4><ul><li>Sed uerspatiem</li><li>Comnisteatusit</li><li>Sed ueratiem</li><li>Comnisteatusit</li></ul></div>
  <div class="footer-col abs" style="left:755px"><h4>Company</h4><ul><li>Sed uterspiciatis</li><li>Sed uerspiciatiem</li><li>Comnisteatusit</li><li>Perspiciatis unde</li></ul></div>
  <div class="footer-col abs" style="left:898px"><h4>Connect</h4>
    <div class="social">
      <svg width="24" height="18" viewBox="0 0 24 18"><rect x="1" y="1" width="22" height="16" fill="#1e1e1e"/><path d="M1 1l11 9 11-9" fill="none" stroke="#fff" stroke-width="1.6"/></svg>
      <span class="dot" aria-label="Social link"></span>
      <span class="dot" aria-label="Social link"></span>
      <span class="dot" aria-label="Social link"></span>
    </div>
  </div>
  <div class="footer-rule abs"></div>
  <p class="copyright abs">© 2018 All Rights are Reserved. Privacy Policy | Terms of Use | Contact</p>
</footer>

</body>
</html>
```